Ward Compass Business Card Design*

We need a business card design for our company Ward Compass. Our company is specialized in providing online consulting services regarding medical institutions, hospitals and doctors. We work with patients worldwide looking to choose between healthcare providers. We have a website you may use as a reference, where we list doctors and clinics worldwide. So we target Medical providers as well as patients worldwide.
Target Market(s)
Medical Providers and patients around the world
Industry/Entity Type
Medical
Contact Information for Business Card
Salwa Kettani
CEO
+90 612 348 2175
info@wardcompass.example
www.wardcompass.example
14 Annakhil 7 H.R.B. Rabat, Morocco
Requirements
Must have
- Company logo/name on one full side, personal info and smaller logo and company name on the other side.
Nice to have
- Smart and elegant design

```html
<!DOCTYPE html>
<html lang="en">
<head>
<meta charset="utf-8">
<title>Ward Compass Business Card</title>
<link rel="stylesheet" href="https://fonts.googleapis.com/css2?family=Open+Sans:wght@400;600;700&display=swap">
<style>
  :root {
    --navy: #173a66;
    --grey: #808080;
    --grey-light: #9a9a9a;
    --text: #3a3a3a;
    --paper: #ffffff;
    --backdrop: #e6e6e6;
  }
  * { box-sizing: border-box; margin: 0; padding: 0; }
  html, body { width: 1200px; height: 768px; overflow: hidden; }
  body {
    background: var(--backdrop);
    font-family: "Open Sans", Arial, sans-serif;
    display: flex;
    align-items: center;
    justify-content: center;
    gap: 40px;
  }
  .card {
    width: 540px;
    height: 310px;
    position: relative;
    overflow: hidden;
    box-shadow: 0 6px 18px rgba(0,0,0,0.18);
  }
  /* Back side */
  .card-back {
    background: var(--grey);
    color: var(--paper);
    display: flex;
    flex-direction: column;
    align-items: center;
  }
  .back-brand {
    margin-top: 110px;
    display: flex;
    align-items: center;
    gap: 14px;
  }
  .back-brand .dot {
    width: 34px; height: 34px;
    border-radius: 50%;
    background: var(--paper);
  }
  .back-brand .name {
    font-size: 30px;
    font-weight: 600;
    letter-spacing: 2px;
    text-transform: uppercase;
  }
  .back-url {
    position: absolute;
    bottom: 40px;
    font-size: 13px;
    letter-spacing: 6px;
  }
  /* Front side */
  .card-front { background: var(--paper); }
  .front-brand {
    position: absolute;
    left: 34px;
    top: 118px;
    display: flex;
    align-items: center;
    gap: 10px;
  }
  .front-brand .dot {
    width: 28px; height: 28px;
    border-radius: 50%;
    background: var(--navy);
  }
  .front-brand .name {
    font-size: 19px;
    font-weight: 600;
    letter-spacing: 1px;
    color: var(--navy);
    text-transform: uppercase;
  }
  .divider {
    position: absolute;
    left: 290px;
    top: 70px;
    width: 1px;
    height: 150px;
    background: #bdbdbd;
  }
  .details {
    position: absolute;
    left: 310px;
    top: 70px;
    color: var(--text);
    font-size: 13px;
    line-height: 1.35;
  }
  .person-name {
    font-size: 19px;
    font-weight: 700;
    color: var(--navy);
    line-height: 1.1;
  }
  .person-role { color: var(--grey); font-size: 13px; margin-bottom: 8px; }
  .address { margin-bottom: 4px; }
  .contact-row { display: flex; align-items: center; gap: 7px; }
  .contact-row svg { width: 11px; height: 11px; flex: none; fill: var(--navy); }
  .bottom-band {
    position: absolute;
    left: 0; right: 0; bottom: 0;
    height: 10px;
    display: flex;
  }
  .bottom-band .navy { width: 64%; background: var(--navy); }
  .bottom-band .rest { flex: 1; background: var(--grey); margin-left: 3px; }
</style>
</head>
<body>
  <section class="card card-back" aria-label="Card back">
    <div class="back-brand">
      <span class="dot"></span>
      <span class="name">Ward Compass</span>
    </div>
    <p class="back-url">www.wardcompass.example</p>
  </section>

  <section class="card card-front" aria-label="Card front">
    <div class="front-brand">
      <span class="dot"></span>
      <span class="name">Ward Compass</span>
    </div>
    <div class="divider"></div>
    <div class="details">
      <p class="person-name">Salwa Kettani</p>
      <p class="person-role">CEO</p>
      <p class="address">14 Annakhil 7<br>H.R.B. Rabat, Morocco</p>
      <p class="contact-row">
        <svg viewBox="0 0 12 12" aria-hidden="true"><path d="M2 4h8v6H2z M1 3c1-2 9-2 10 0v1H9V3H3v1H1z"/></svg>
        +90 612 348 2175
      </p>
      <p class="contact-row">
        <svg viewBox="0 0 12 12" aria-hidden="true"><path d="M1 3h10v6H1z M1 3l5 4 5-4" stroke="#fff" stroke-width="0.8"/></svg>
        info@wardcompass.example
      </p>
      <p class="contact-row">
        <svg viewBox="0 0 12 12" aria-hidden="true"><circle cx="6" cy="6" r="5.5"/></svg>
        www.wardcompass.example
      </p>
    </div>
    <div class="bottom-band"><span class="navy"></span><span class="rest"></span></div>
  </section>
</body>
</html>
```